Corvane Capital Business Cards

These are professional business cards that are for my family office.
Put fake emails and phone numbers as of now until I finalize those components. This family office controls my families investments, assets, and future. The cards should be professional.
..
.
.
.
I just uploaded another variation of a logo I would like to see as a business card to I am inbeteen which logo to use

Target Market(s)

business

Industry/Entity Type

business

Contact Information for Business Card

Professional, wealth related, finance related.

Requirements
Must have
• Logo

```html
<!DOCTYPE html>
<html lang="en">
<head>
<meta charset="utf-8">
<title>Corvane Capital Business Cards</title>
<link href="https://fonts.googleapis.com/css2?family=Playfair+Display:wght@400&family=Tinos:wght@400;700&display=swap" rel="stylesheet">
<style>
  :root {
    --backdrop: #e3e3e1;
    --paper: #ffffff;
    --ink: #111111;
    --gold: #c6ad6f;
    --card-w: 580px;
    --card-h: 332px;
  }
  * { box-sizing: border-box; margin: 0; padding: 0; }
  html, body {
    width: 1200px;
    height: 900px;
    overflow: hidden;
    background: var(--backdrop);
  }
  .canvas {
    position: relative;
    width: 1200px;
    height: 900px;
  }
  .card {
    position: absolute;
    width: var(--card-w);
    height: var(--card-h);
    background: var(--paper);
    box-shadow: 0 10px 28px rgba(0, 0, 0, 0.16);
    overflow: hidden;
  }

  /* Front */
  .card--front { left: 70px; top: 80px; }
  .front-wordmark {
    position: absolute;
    inset: 0;
    display: flex;
    align-items: center;
    justify-content: center;
    gap: 18px;
  }
  .brand-square {
    width: 22px;
    height: 22px;
    background: var(--gold);
  }
  .front-name {
    font-family: "Playfair Display", serif;
    font-weight: 400;
    font-size: 40px;
    letter-spacing: 0.08em;
    text-transform: uppercase;
    color: var(--ink);
  }

  /* Back */
  .card--back { right: 70px; bottom: 80px; }
  .back-wordmark {
    position: absolute;
    left: 44px;
    top: 96px;
    width: 240px;
    display: flex;
    align-items: center;
    gap: 14px;
  }
  .back-name {
    font-family: "Playfair Display", serif;
    font-weight: 400;
    font-size: 34px;
    line-height: 1.1;
    letter-spacing: 0.06em;
    text-transform: uppercase;
    color: var(--ink);
  }
  .divider {
    position: absolute;
    left: 300px;
    top: 58px;
    width: 1.5px;
    height: 168px;
    background: var(--gold);
  }
  .contact {
    position: absolute;
    left: 322px;
    top: 66px;
    font-family: "Tinos", serif;
    color: var(--ink);
  }
  .person-name {
    font-weight: 700;
    font-size: 21px;
    line-height: 1.1;
  }
  .person-name .surname { color: var(--gold); }
  .person-role {
    font-size: 15px;
    margin-top: 4px;
  }
  .role-rule {
    width: 16px;
    height: 3px;
    background: var(--gold);
    margin: 10px 0 22px;
  }
  .contact-line {
    display: flex;
    align-items: center;
    gap: 8px;
    font-size: 14px;
    line-height: 1;
    margin-bottom: 9px;
  }
  .contact-line svg { width: 13px; height: 13px; flex: none; }
  .footer-band {
    position: absolute;
    left: 0;
    bottom: 0;
    width: 100%;
    height: 24px;
  }
</style>
</head>
<body>
<main class="canvas">

  <section class="card card--front" aria-label="Card front">
    <div class="front-wordmark">
      <span class="brand-square"></span>
      <span class="front-name">Corvane Capital</span>
    </div>
  </section>

  <section class="card card--back" aria-label="Card back">
    <div class="back-wordmark">
      <span class="brand-square"></span>
      <span class="back-name">Corvane<br>Capital</span>
    </div>

    <span class="divider"></span>

    <div class="contact">
      <p class="person-name">Elias <span class="surname">Morrow</span></p>
      <p class="person-role">Founder</p>
      <span class="role-rule" style="display:block"></span>
      <p class="contact-line">
        <svg viewBox="0 0 16 16" aria-hidden="true"><path fill="#c6ad6f" d="M2 6c0-2 2-3 6-3s6 1 6 3v1h-3V5.5C10 5 9 4.8 8 4.8S6 5 5 5.5V7H2zM4 8h8l1.5 5h-11z"/></svg>
        555-210-4830
      </p>
      <p class="contact-line">
        <svg viewBox="0 0 16 16" aria-hidden="true"><path fill="#c6ad6f" d="M1 3h14v10H1zM2 4.2v.3l6 4.3 6-4.3v-.3z"/></svg>
        office@corvanecapital.com
      </p>
    </div>

    <svg class="footer-band" viewBox="0 0 580 24" preserveAspectRatio="none" aria-hidden="true">
      <polygon points="0,0 332,0 324,24 0,24" fill="#c6ad6f"/>
      <polygon points="338,0 580,0 580,24 330,24" fill="#111111"/>
    </svg>
  </section>

</main>
</body>
</html>
```